Kestrelway Financial Plans

I am looking for a complete resdesign of my small financial presentation. This is a Word Doc/PDF that I print off when meeting with people in private. I often present my "two pager" that I have been using for years and years. It tells them the basics of what I do, how I help people and foundational financial principles.

I have recently gone out on my own in business and have completely rebranded. This presentation is my most used tool, so it is the first of many things I would like to redo. I am hoping it will somehow coordinate with the colors of my business, not necessarily the EXACT same 3 colors everywhere, but have the design colors compliment.

I've uploaded all my logo designs, as well as the current "two-pager". I am not against it going to 3 pages if needed. As it will still land on 2 pages with duplex printing.

It has always been VERY simple. I am wanting it built into a more professional and design specific format, to show off my branding, without being over cluttered.

I am completely open to ANY graphics changes. Obviously some are very novice, the house on the last page has always been overly simplified.

```html
<!DOCTYPE html>
<html lang="en">
<head>
<meta charset="utf-8">
<title>Kestrelway Financial Plans – The Financial Challenge</title>
<link href="https://fonts.googleapis.com/css2?family=Montserrat:wght@400;600;700;800&family=Open+Sans:wght@400;600;700&display=swap" rel="stylesheet">
<style>
  :root{
    --green:#2bb24c;
    --green-dark:#1f8f3b;
    --green-pale:#e3f4e7;
    --ink:#33393e;
    --grey:#6b7278;
    --grey-mid:#9aa0a5;
    --grey-light:#e4e6e8;
    --paper:#ffffff;
    --backdrop:#ededee;
  }
  *{box-sizing:border-box;margin:0;padding:0}
  html,body{width:885px;height:1200px;overflow:hidden;background:var(--backdrop)}
  body{font-family:"Open Sans",Arial,sans-serif;color:var(--ink);position:relative}

  .page{position:absolute;top:290px;width:420px;height:594px;background:var(--paper);
    box-shadow:0 4px 18px rgba(0,0,0,.14);padding:22px 24px 0;overflow:hidden}
  .page-front{left:15px}
  .page-back{left:450px}

  .brand{display:flex;align-items:center;gap:6px}
  .brand-square{width:8px;height:8px;background:var(--green)}
  .brand-name{font-family:"Montserrat",sans-serif;font-weight:800;font-size:17px;letter-spacing:.5px;line-height:1;color:var(--ink)}
  .brand-sub{font-family:"Montserrat",sans-serif;font-weight:600;font-size:6px;letter-spacing:2.4px;color:var(--grey);margin:3px 0 0 14px}

  .title{margin-top:12px;font-family:"Montserrat",sans-serif;font-weight:600;color:var(--green);font-size:31px;line-height:1.02;letter-spacing:-.5px}
  .title-rule{height:4px;background:var(--green);margin-top:10px}

  .challenges{display:grid;grid-template-columns:repeat(3,1fr);gap:12px;margin-top:12px}
  .challenge h3{font-family:"Montserrat",sans-serif;font-weight:800;font-size:11px;color:var(--green);margin-bottom:5px}
  .challenge p{font-size:6.4px;line-height:1.5;color:var(--grey)}
  .challenge-body{display:flex;gap:6px;align-items:flex-start}
  .challenge-body svg{flex:none}

  .section-head{margin-top:16px;text-align:center;font-family:"Montserrat",sans-serif;font-weight:800;font-size:11.5px;color:var(--ink)}
  .services{display:flex;justify-content:space-between;margin-top:10px}
  .service{text-align:center;width:50px}
  .service svg{display:block;margin:0 auto 3px}
  .service span{font-size:5px;font-weight:700;color:var(--grey);text-transform:uppercase;letter-spacing:.3px}

  .band{margin-top:12px;background:var(--green);color:#fff;text-align:center;font-family:"Montserrat",sans-serif;font-weight:700;font-size:10px;padding:5px 0;letter-spacing:.5px}

  .method{display:flex;gap:8px;margin-top:12px;align-items:center}
  .chart{width:210px;height:150px;flex:none}
  .savings{display:flex;align-items:stretch;gap:6px;flex:1}
  .savings-label{writing-mode:vertical-rl;transform:rotate(180deg);font-family:"Montserrat",sans-serif;font-weight:800;font-size:20px;color:var(--green);letter-spacing:1.5px}
  .savings-list{list-style:none;display:flex;flex-direction:column;justify-content:center;gap:9px;border-left:2px solid var(--green);padding-left:8px}
  .savings-list li{display:flex;align-items:center;gap:5px;font-size:7.5px;font-weight:600;color:var(--ink)}

  .footer{position:absolute;left:0;right:0;bottom:0;height:22px;background:var(--ink);color:#fff;display:flex;align-items:center;justify-content:space-between;padding:0 24px;font-size:6px}
  .footer-brand{font-family:"Montserrat",sans-serif;font-weight:700;letter-spacing:1px;color:var(--green)}

  /* back page */
  .rule-head{display:flex;align-items:center;justify-content:space-between;margin-top:14px}
  .rule-tag{background:var(--green);color:#fff;font-family:"Montserrat",sans-serif;font-weight:800;font-size:10px;padding:4px 10px;letter-spacing:.5px}
  .rule-note{font-size:6px;color:var(--grey)}
  .rule-tables{display:grid;grid-template-columns:1fr 1fr;gap:14px;margin-top:8px}
  .rate-table{width:100%;border-collapse:collapse;font-size:6.2px}
  .rate-table th{background:var(--ink);color:#fff;font-weight:700;padding:3px 4px;text-align:center}
  .rate-table th.rate{background:var(--green)}
  .rate-table td{padding:2.6px 4px;text-align:center;border-bottom:1px solid var(--grey-light);color:var(--ink)}
  .rate-table tr:nth-child(even) td{background:#f5f6f7}

  .doubling{display:grid;grid-template-columns:repeat(4,1fr);gap:7px;margin-top:14px}
  .double-card{background:var(--green);color:#fff;text-align:center;padding:7px 2px 8px}
  .double-card .pct{display:block;font-family:"Montserrat",sans-serif;font-weight:700;font-size:8px;opacity:.9}
  .double-card .every{display:block;font-size:6px;font-weight:600;margin-top:3px;letter-spacing:.5px}
  .double-card .years{display:block;font-family:"Montserrat",sans-serif;font-weight:800;font-size:13px;line-height:1.1}

  .house{display:block;margin:14px auto 0;width:372px;height:232px}
</style>
</head>
<body>

<main class="page page-front">
  <header>
    <div class="brand"><span class="brand-square"></span><span class="brand-name">KESTRELWAY</span></div>
    <div class="brand-sub">FINANCIAL PLANS</div>
  </header>

  <h1 class="title">THE FINANCIAL<br>CHALLENGE</h1>
  <div class="title-rule"></div>

  <section class="challenges">
    <article class="challenge">
      <h3>SAVINGS</h3>
      <div class="challenge-body">
        <svg width="18" height="18" viewBox="0 0 34 34"><rect x="4" y="12" width="26" height="18" rx="3" fill="var(--green)"/><circle cx="17" cy="8" r="5" fill="none" stroke="var(--ink)" stroke-width="2.5"/></svg>
        <p>Only 1 in 3 families have saved enough for retirement and most rely on a single income stream to cover every need.</p>
      </div>
    </article>
    <article class="challenge">
      <h3>DEBT</h3>
      <div class="challenge-body">
        <svg width="18" height="18" viewBox="0 0 34 34"><rect x="3" y="8" width="28" height="18" rx="3" fill="var(--ink)"/><rect x="3" y="12" width="28" height="4" fill="var(--green)"/></svg>
        <p>Household debt keeps rising while interest costs quietly eat into the money meant for the future.</p>
      </div>
    </article>
    <article class="challenge">
      <h3>INSURANCE</h3>
      <div class="challenge-body">
        <svg width="18" height="18" viewBox="0 0 34 34"><path d="M3 18a14 14 0 0 1 28 0z" fill="var(--green)"/><path d="M17 18v10a3 3 0 0 1-6 0" fill="none" stroke="var(--ink)" stroke-width="2.5"/></svg>
        <p>Many families carry too little cover, leaving loved ones exposed if the unexpected happens.</p>
      </div>
    </article>
  </section>

  <h2 class="section-head">WHO ARE WE AND WHAT DO WE DO?</h2>
  <section class="services">
    <div class="service"><svg width="20" height="18" viewBox="0 0 34 30"><path d="M3 14 17 3l14 11v14H3z" fill="var(--ink)"/></svg><span>Budgeting</span></div>
    <div class="service"><svg width="20" height="18" viewBox="0 0 34 30"><rect x="3" y="8" width="28" height="18" rx="9" fill="var(--green)"/></svg><span>Savings</span></div>
    <div class="service"><svg width="20" height="18" viewBox="0 0 34 30"><rect x="4" y="18" width="6" height="10" fill="var(--ink)"/><rect x="14" y="11" width="6" height="17" fill="var(--ink)"/><rect x="24" y="4" width="6" height="24" fill="var(--green)"/></svg><span>Investing</span></div>
    <div class="service"><svg width="20" height="18" viewBox="0 0 34 30"><path d="M17 2 30 7v8c0 7-6 12-13 14C10 27 4 22 4 15V7z" fill="var(--ink)"/></svg><span>Protection</span></div>
    <div class="service"><svg width="20" height="18" viewBox="0 0 34 30"><circle cx="17" cy="15" r="12" fill="var(--green)"/><path d="M17 8v7l5 3" stroke="#fff" stroke-width="2.5" fill="none"/></svg><span>Retirement</span></div>
    <div class="service"><svg width="20" height="18" viewBox="0 0 34 30"><path d="M2 12 17 5l15 7-15 7z" fill="var(--ink)"/><path d="M8 15v7c6 4 12 4 18 0v-7" fill="var(--ink)"/></svg><span>Education</span></div>
    <div class="service"><svg width="20" height="18" viewBox="0 0 34 30"><rect x="6" y="3" width="22" height="25" rx="2" fill="var(--green)"/><path d="M10 10h14M10 15h14M10 20h9" stroke="#fff" stroke-width="2"/></svg><span>Estate</span></div>
  </section>

  <div class="band">HOW ARE WE DOING IT?</div>

  <section class="method">
    <svg class="chart" viewBox="0 0 210 150" role="img" aria-label="Pie chart of income split into expenses, debt and savings">
      <g transform="translate(70 75) rotate(-90)">
        <circle r="32" fill="none" stroke="var(--green)" stroke-width="64" stroke-dasharray="80.4 201.1"/>
        <circle r="32" fill="none" stroke="var(--ink)" stroke-width="64" stroke-dasharray="0 80.4 60.3 201.1"/>
        <circle r="32" fill="none" stroke="var(--grey)" stroke-width="64" stroke-dasharray="0 140.7 30.2 201.1"/>
        <circle r="32" fill="none" stroke="var(--grey-light)" stroke-width="64" stroke-dasharray="0 170.9 30.2 201.1"/>
      </g>
      <circle cx="70" cy="75" r="64" fill="none" stroke="#fff" stroke-width="1"/>
      <g font-family="Open Sans, sans-serif" font-size="7" font-weight="600" fill="var(--ink)">
        <rect x="148" y="40" width="8" height="8" fill="var(--green)"/><text x="160" y="47">Income</text>
        <rect x="148" y="60" width="8" height="8" fill="var(--ink)"/><text x="160" y="67">Expenses</text>
        <rect x="148" y="80" width="8" height="8" fill="var(--grey)"/><text x="160" y="87">Debt</text>
        <rect x="148" y="100" width="8" height="8" fill="var(--grey-light)" stroke="var(--grey)" stroke-width=".8"/><text x="160" y="107">Savings</text>
      </g>
    </svg>
    <div class="savings">
      <div class="savings-label">SAVINGS</div>
      <ul class="savings-list">
        <li><svg width="9" height="9" viewBox="0 0 16 16"><path d="M2 8l4 4 8-9" stroke="var(--green)" stroke-width="3" fill="none"/></svg>Retirement savings</li>
        <li><svg width="9" height="9" viewBox="0 0 16 16"><path d="M2 8l4 4 8-9" stroke="var(--green)" stroke-width="3" fill="none"/></svg>Children's education</li>
        <li><svg width="9" height="9" viewBox="0 0 16 16"><path d="M2 8l4 4 8-9" stroke="var(--green)" stroke-width="3" fill="none"/></svg>Property protection</li>
        <li><svg width="9" height="9" viewBox="0 0 16 16"><path d="M2 8l4 4 8-9" stroke="var(--green)" stroke-width="3" fill="none"/></svg>Emergency funds</li>
      </ul>
    </div>
  </section>

  <footer class="footer">
    <span class="footer-brand">KESTRELWAY FINANCIAL PLANS</span>
    <span>Helping families build lasting financial strength</span>
  </footer>
</main>

<main class="page page-back">
  <header>
    <div class="brand"><span class="brand-square"></span><span class="brand-name">KESTRELWAY</span></div>
    <div class="brand-sub">FINANCIAL PLANS</div>
  </header>

  <div class="rule-head">
    <span class="rule-tag">RULE OF 72</span>
    <span class="rule-note">72 ÷ interest rate = years for money to double</span>
  </div>

  <section class="rule-tables">
    <table class="rate-table">
      <thead><tr><th>AGE</th><th class="rate">AT 6%</th><th>AGE</th><th class="rate">AT 6%</th></tr></thead>
      <tbody>
        <tr><td>29</td><td>$10,000</td><td>53</td><td>$160,000</td></tr>
        <tr><td>35</td><td>$20,000</td><td>59</td><td>$320,000</td></tr>
        <tr><td>41</td><td>$40,000</td><td>65</td><td>$640,000</td></tr>
        <tr><td>47</td><td>$80,000</td><td>71</td><td>$1,280,000</td></tr>
      </tbody>
    </table>
    <table class="rate-table">
      <thead><tr><th>AGE</th><th class="rate">AT 12%</th><th>AGE</th><th class="rate">AT 12%</th></tr></thead>
      <tbody>
        <tr><td>29</td><td>$10,000</td><td>53</td><td>$160,000</td></tr>
        <tr><td>35</td><td>$20,000</td><td>59</td><td>$320,000</td></tr>
        <tr><td>41</td><td>$40,000</td><td>65</td><td>$640,000</td></tr>
        <tr><td>47</td><td>$80,000</td><td>71</td><td>$1,280,000</td></tr>
      </tbody>
    </table>
  </section>

  <section class="doubling">
    <div class="double-card"><span class="pct">4%</span><span class="every">EVERY</span><span class="years">18 YEARS</span></div>
    <div class="double-card"><span class="pct">6%</span><span class="every">EVERY</span><span class="years">12 YEARS</span></div>
    <div class="double-card"><span class="pct">8%</span><span class="every">EVERY</span><span class="years">9 YEARS</span></div>
    <div class="double-card"><span class="pct">12%</span><span class="every">EVERY</span><span class="years">6 YEARS</span></div>
  </section>

  <svg class="house" viewBox="0 0 372 232" role="img" aria-label="House diagram of a financial plan">
    <g font-family="Open Sans, sans-serif">
      <!-- roof -->
      <path d="M6 92 186 8 366 92" fill="none" stroke="var(--green)" stroke-width="7" stroke-linejoin="round"/>
      <path d="M30 92 186 20 342 92z" fill="var(--green-pale)"/>
      <rect x="156" y="46" width="60" height="20" fill="var(--ink)"/>
      <text x="186" y="60" text-anchor="middle" font-family="Montserrat, sans-serif" font-weight="800" font-size="10" fill="#fff">TAXES</text>
      <!-- walls -->
      <rect x="30" y="92" width="312" height="102" fill="#fff" stroke="var(--grey-mid)" stroke-width="1.5"/>
      <!-- left column -->
      <rect x="40" y="100" width="140" height="40" fill="var(--grey-light)"/>
      <text x="48" y="114" font-size="8" font-weight="700" fill="var(--ink)">HOME</text>
      <text x="48" y="126" font-size="6" fill="var(--grey)">Mortgage paid down sooner</text>
      <text x="48" y="134" font-size="6" fill="var(--grey)">with a clear payoff plan</text>
      <rect x="40" y="146" width="140" height="40" fill="var(--grey-light)"/>
      <text x="48" y="160" font-size="8" font-weight="700" fill="var(--ink)">TFSA</text>
      <text x="48" y="172" font-size="6" fill="var(--grey)">Tax-free growth for goals</text>
      <text x="48" y="180" font-size="6" fill="var(--grey)">and emergency savings</text>
      <!-- right column -->
      <rect x="192" y="100" width="140" height="40" fill="var(--grey-light)"/>
      <text x="200" y="114" font-size="8" font-weight="700" fill="var(--ink)">RRSP</text>
      <text x="200" y="126" font-size="6" fill="var(--grey)">Retirement savings with</text>
      <text x="200" y="134" font-size="6" fill="var(--grey)">tax deferred growth</text>
      <rect x="192" y="146" width="140" height="40" fill="var(--grey-light)"/>
      <text x="200" y="160" font-size="8" font-weight="700" fill="var(--ink)">PERM LIFE</text>
      <text x="200" y="172" font-size="6" fill="var(--grey)">Lifelong cover that builds</text>
      <text x="200" y="180" font-size="6" fill="var(--grey)">value for your estate</text>
      <!-- foundation -->
      <rect x="20" y="196" width="332" height="16" fill="var(--green)"/>
      <text x="30" y="207" font-size="7" font-weight="700" fill="#fff">LIFE INSURANCE / ILLNESS</text>
      <text x="342" y="207" font-size="7" font-weight="700" fill="#fff" text-anchor="end">DEBT MANAGEMENT</text>
      <rect x="20" y="214" width="332" height="16" fill="var(--ink)"/>
      <text x="30" y="225" font-size="7" font-weight="700" fill="#fff">CRITICAL / DISABILITY</text>
      <text x="342" y="225" font-size="7" font-weight="700" fill="#fff" text-anchor="end">CASH FLOW</text>
    </g>
  </svg>

  <footer class="footer">
    <span class="footer-brand">KESTRELWAY FINANCIAL PLANS</span>
    <span>Helping families build lasting financial strength</span>
  </footer>
</main>

</body>
</html>
```